Lunelle Rosa Hair Fancy Business Card’s

I want my business cards to be elite, original and very classy. I want the business cards to match the colors of my logo and to match the design posted. I would love the design of the picture I posted

I want the card all white .
The dripping on the top of the card I want it to match the pink color in my logo that’s also posted .
I need my logo on the business card !
I need my Instagram- @lunelle.rosa.hair__
And my phone number - 555 207 3962

Target Market(s)

My target market is young woman age 23 to older woman to the age of 65
I want both older and younger women to love my design . I don’t want any cheap looking business cards

Industry/Entity Type

Hair And Beauty

Contact Information for Business Card

Add my logo
Add my Instagram- @lunelle.rosa.hair__
My number - 555 207 3962
My website- www.lunellerosahair.example

Font styles to use
Serif
Script

Colors
ffffff
e667a6
e34298

Requirements
Must have
• The business cards must have my logo, my number , my website, and my Instagram!
Nice to have
• Nice to have glitter words that match my logo
• The business cards must look classy and mature
• I want them to be very unique!!
Should not have
• Should not have any colors that doesn’t match my logo ! This is very important! Please

```html
<!DOCTYPE html>
<html lang="en">
<head>
<meta charset="utf-8">
<title>Lunelle Rosa Hair – Business Card</title>
<link href="https://fonts.googleapis.com/css2?family=Cinzel:wght@500;600&family=Poppins:wght@400&display=swap" rel="stylesheet">
<style>
  :root {
    --backdrop: #2b2b2e;
    --pink: #e34298;
    --pink-soft: #e667a6;
    --white: #ffffff;
    --charcoal: #3f3f46;
    --silver-light: #d9d9dc;
    --silver-dark: #8e8e93;
  }
  * { box-sizing: border-box; margin: 0; padding: 0; }
  html, body {
    width: 1125px; height: 1200px; overflow: hidden;
    background: var(--backdrop);
  }
  .canvas { position: relative; width: 1125px; height: 1200px; }

  .card {
    position: absolute; left: 171px; width: 826px; height: 472px;
    overflow: hidden;
  }
  .card--front { top: 106px; background: var(--white); }
  .card--back { top: 640px; height: 470px; background: var(--charcoal); }

  .contact-panel {
    position: absolute; left: 0; top: 0; width: 365px; height: 100%;
    background: var(--pink); color: var(--white);
  }
  .holder-name {
    position: absolute; left: 39px; top: 96px;
    font-family: "Cinzel", serif; font-weight: 600; font-size: 32px; letter-spacing: 0.5px;
  }
  .holder-title {
    position: absolute; left: 40px; top: 134px;
    font-family: "Cinzel", serif; font-weight: 600; font-size: 18px; letter-spacing: 0.5px;
  }
  .divider {
    position: absolute; left: 41px; top: 189px; width: 301px; height: 2px;
    background: var(--white);
  }
  .contact-list { list-style: none; position: absolute; left: 38px; top: 230px; }
  .contact-item {
    display: flex; align-items: center; height: 39px;
    font-family: "Poppins", sans-serif; font-size: 19px;
  }
  .contact-icon {
    width: 26px; height: 26px; background: var(--white); margin-right: 13px;
    display: flex; align-items: center; justify-content: center;
  }
  .contact-icon svg { width: 15px; height: 15px; }

  .glitter-edge {
    position: absolute; right: 0; top: 0; width: 30px; height: 100%;
    background: linear-gradient(90deg, var(--silver-dark), var(--silver-light) 45%, var(--silver-dark));
  }

  .brand-name {
    position: absolute; text-align: center; color: var(--pink);
    font-family: "Cinzel", serif; font-weight: 600; line-height: 1.15; letter-spacing: 2px;
    text-transform: uppercase;
  }
  .card--front .brand-name { left: 365px; width: 431px; top: 180px; font-size: 36px; }
  .card--back .brand-name { left: 0; width: 826px; top: 165px; font-size: 60px; }
</style>
</head>
<body>
<main class="canvas">
  <section class="card card--front">
    <div class="contact-panel">
      <h1 class="holder-name">Daniel Hartley</h1>
      <p class="holder-title">President</p>
      <div class="divider"></div>
      <ul class="contact-list">
        <li class="contact-item">
          <span class="contact-icon"><svg viewBox="0 0 24 24"><path fill="#e34298" d="M6.6 10.8a15.1 15.1 0 0 0 6.6 6.6l2.2-2.2c.3-.3.7-.4 1-.2 1.1.4 2.3.6 3.6.6.6 0 1 .4 1 1V20c0 .6-.4 1-1 1A17 17 0 0 1 3 4c0-.6.4-1 1-1h3.5c.6 0 1 .4 1 1 0 1.3.2 2.5.6 3.6.1.3 0 .7-.2 1z"/></svg></span>
          555 207 3962
        </li>
        <li class="contact-item">
          <span class="contact-icon"><svg viewBox="0 0 24 24"><rect x="5" y="5" width="14" height="14" fill="#e34298"/></svg></span>
          @lunelle.rosa.hair__
        </li>
        <li class="contact-item">
          <span class="contact-icon"><svg viewBox="0 0 24 24"><rect x="3" y="6" width="18" height="12" fill="#e34298"/><path d="M3 6l9 7 9-7" fill="none" stroke="#fff" stroke-width="1.6"/></svg></span>
          info@lunellerosahair.example
        </li>
        <li class="contact-item">
          <span class="contact-icon"><svg viewBox="0 0 24 24"><circle cx="12" cy="12" r="9" fill="#e34298"/><path d="M3 12h18M12 3c3 3 3 15 0 18M12 3c-3 3-3 15 0 18" fill="none" stroke="#fff" stroke-width="1.3"/></svg></span>
          www.lunellerosahair.example
        </li>
      </ul>
    </div>
    <p class="brand-name">Lunelle Rosa Hair</p>
    <div class="glitter-edge" role="img" aria-label="Silver glitter strip along the card edge"></div>
  </section>

  <section class="card card--back">
    <p class="brand-name">Lunelle Rosa Hair</p>
  </section>
</main>
</body>
</html>
```